Fitness Equipment Repair Business Needs a Catchy New Business Card

We have an existing business card, however, it is quite plain and boring. We are expanding primarily in the commercial area (gyms, studios, apartment complexes etc). The business card will serve as eye candy to those managers/owners that can't be met for a face to face.
Originally I was planning for a brochure as well, but all of our information is better summarized on our website. (brightloopservice.ca).
I would like the card to match the colour scheme of the website and utilize the logo. It should have a professional clean feel to it, however, a little colouring outside the lines wouldn't hurt.
The example card is for my service technician (Colin Marsh). If possible I would like to be able to edit the text to use for more than one person.

Industry/Entity Type

Appliance Repair

Contact Information for Business Card

Clean, crisp and professional but needs to be eye catching. Preferably using the black, white and red colour scheme matching the website. Double sided would be nice, but is not necessary.

Colors
ec1f27
ffffff
000000

Requirements
Must have
• Must be able to edit name, phone number and title to use for multiple people. Must show the company website (brightloopservice.ca).

```html
<!DOCTYPE html>
<html lang="en">
<head>
<meta charset="utf-8">
<title>Brightloop Service – Business Card</title>
<link rel="stylesheet" href="https://fonts.googleapis.com/css2?family=Marcellus+SC&family=Open+Sans:wght@400;600&display=swap">
<style>
  :root {
    --red: #d2333b;
    --black: #000000;
    --white: #ffffff;
    --stage: #e9e6e3;
    --ink: #111111;
  }
  * { box-sizing: border-box; margin: 0; padding: 0; }
  html, body { width: 1200px; height: 900px; overflow: hidden; }
  body {
    background: var(--stage);
    position: relative;
    font-family: "Open Sans", Arial, sans-serif;
  }
  .card {
    position: absolute;
    overflow: hidden;
    box-shadow: 0 6px 18px rgba(0,0,0,.18);
  }

  /* Front */
  .card-front {
    left: 78px; top: 34px; width: 588px; height: 364px;
    background: var(--red);
  }
  .front-header {
    height: 165px;
    background: var(--black);
    display: flex;
    align-items: center;
  }
  .brand-mark {
    width: 118px;
    display: flex; flex-direction: column; align-items: center; gap: 6px;
    margin-left: 22px;
  }
  .brand-mark .dot { width: 34px; height: 34px; border-radius: 50%; background: var(--red); }
  .brand-mark .initials {
    font-weight: 600; color: var(--white); font-size: 22px; letter-spacing: 1px;
  }
  .company-name {
    font-family: "Marcellus SC", Georgia, serif;
    font-weight: 400;
    color: var(--white);
    font-size: 41px;
    margin-top: -2px;
    letter-spacing: .3px;
    white-space: nowrap;
  }
  .person { padding: 18px 0 0 31px; color: var(--white); }
  .person-name { font-size: 20px; font-weight: 600; line-height: 1.2; }
  .person-title { font-size: 16px; line-height: 1.35; }
  .contact-list { list-style: none; margin-top: 13px; }
  .contact-list li {
    display: flex; align-items: center; gap: 18px;
    font-size: 16px; line-height: 21.7px;
  }
  .contact-list svg { width: 12px; height: 12px; fill: var(--white); flex: none; }
  .address { font-size: 16px; margin-top: 2px; }

  /* Back */
  .card-back {
    left: 388px; top: 505px; width: 567px; height: 352px;
    background: var(--white);
  }
  .back-band { position: absolute; left: 0; top: 0; }
  .back-mark {
    position: absolute; left: 205px; top: 110px; width: 160px; height: 135px;
    display: flex; flex-direction: column; align-items: center; justify-content: center; gap: 8px;
  }
  .back-mark .dot { width: 44px; height: 44px; border-radius: 50%; background: var(--red); }
  .back-mark .initials {
    font-weight: 600; color: var(--red); font-size: 30px; letter-spacing: 2px;
  }
  .tagline {
    position: absolute; left: 0; right: 0; top: 276px;
    text-align: center; font-size: 15.5px; color: var(--ink);
  }
</style>
</head>
<body>

<section class="card card-front">
  <header class="front-header">
    <div class="brand-mark">
      <span class="dot"></span>
      <span class="initials">BLS</span>
    </div>
    <h1 class="company-name">Brightloop Service</h1>
  </header>
  <div class="person">
    <p class="person-name">Colin Marsh</p>
    <p class="person-title">Managing Director</p>
    <ul class="contact-list">
      <li><svg viewBox="0 0 24 24"><path d="M6.6 10.8c1.4 2.8 3.8 5.1 6.6 6.6l2.2-2.2c.3-.3.7-.4 1-.2 1.1.4 2.3.6 3.6.6.6 0 1 .4 1 1V20c0 .6-.4 1-1 1C10.6 21 3 13.4 3 4c0-.6.4-1 1-1h3.5c.6 0 1 .4 1 1 0 1.3.2 2.5.6 3.6.1.3 0 .7-.2 1L6.6 10.8z"/></svg>604-555 0142</li>
      <li><svg viewBox="0 0 24 24"><path d="M2 8c0-2 4-4 10-4s10 2 10 4v2h-5V8c-1-1-9-1-10 0v2H2V8zm5 4h10l3 8H4l3-8zm5 2a2.5 2.5 0 100 5 2.5 2.5 0 000-5z"/></svg>604-555 0187</li>
      <li><svg viewBox="0 0 24 24"><path d="M2 5h20v14H2V5zm2 2v.5l8 5 8-5V7H4z"/></svg>info@brightloopservice.ca</li>
      <li><svg viewBox="0 0 24 24"><path d="M12 2a10 10 0 100 20 10 10 0 000-20zm-1 17.9A8 8 0 014.1 11L9 16v1c0 1.1.9 2 2 2v.9zm6.9-2.5c-.3-.8-1-1.4-1.9-1.4h-1v-3c0-.6-.4-1-1-1H8v-2h2c.6 0 1-.4 1-1V7h2c1.1 0 2-.9 2-2v-.4a8 8 0 012.9 12.8z"/></svg>www.brightloopservice.ca</li>
    </ul>
    <p class="address">2210 Kestrel Way, Abbotsford, BC, Canada V2T 0A4</p>
  </div>
</section>

<section class="card card-back">
  <svg class="back-band" width="567" height="352" viewBox="0 0 567 352" aria-hidden="true">
    <path fill="var(--red)" d="M0 110 H198 C160 140 160 210 198 240 H0 Z"/>
    <path fill="var(--red)" d="M567 110 H370 C408 140 408 210 370 240 H567 Z"/>
  </svg>
  <div class="back-mark">
    <span class="dot"></span>
    <span class="initials">BLS</span>
  </div>
  <p class="tagline">When your equipment can't finish their workout, give us a call!</p>
</section>

</body>
</html>
```